Fashion Label Startup Business Card Design

Miriam Kettle is a startup fashion designer based on the Gold Coast in QLD Australia. Miriams label " Verona by Kettle " is based upon taking old world design techniques and infusing them modern twist. The card design should incorporate an old world theme using colours like mustard, ocha, black, white and elements of lace pattern.

Card Details:

Miriam Kettle
Fashion Designer
P: 04 0261 5847
E: veronabykettle@mailbrook.example
W: www.socialpage.example/VEronaByKettle

```html
<!DOCTYPE html>
<html lang="en">
<head>
<meta charset="utf-8">
<title>Verona by Kettle — Business Card</title>
<link rel="stylesheet" href="https://fonts.googleapis.com/css2?family=Gelasio:ital,wght@0,400;1,400&display=swap">
<style>
  :root {
    --backdrop: #e9e6e0;
    --cream: #f1eee6;
    --tan: #c6b99b;
    --tan-light: #d2c6a8;
    --ink: #3d3c40;
    --mustard: #c9a24a;
    --white: #fbf9f4;
  }
  html, body {
    margin: 0;
    width: 1200px;
    height: 1000px;
    overflow: hidden;
    background: var(--backdrop);
  }
  .canvas {
    position: relative;
    width: 1200px;
    height: 1000px;
    font-family: "Gelasio", Georgia, serif;
  }
  .card {
    position: absolute;
    top: 140px;
    width: 442px;
    height: 722px;
    overflow: hidden;
    background: var(--tan);
    box-shadow: 0 4px 14px rgba(0,0,0,0.18);
  }
  .card--front { left: 110px; }
  .card--back { left: 650px; }

  /* front */
  .front__top {
    position: absolute; left: 0; top: 0; width: 100%; height: 255px;
    background: var(--cream);
  }
  .front__lace {
    position: absolute; left: 0; top: 245px; width: 100%; height: 30px;
    background: linear-gradient(var(--white), var(--tan-light));
  }
  .front__dress-form {
    position: absolute; left: 100px; top: 0; width: 240px; height: 700px;
    background: linear-gradient(to bottom, var(--ink) 0%, var(--ink) 45%, rgba(61,60,64,0.35) 70%, rgba(61,60,64,0) 100%);
    border-radius: 120px 120px 0 0;
  }
  .brand {
    position: absolute; left: 0; top: 395px; width: 100%;
    text-align: center; color: var(--ink); font-weight: 400;
    line-height: 1;
  }
  .brand__word { display: block; font-size: 66px; }
  .brand__by { display: block; font-size: 34px; margin: 2px 0 4px; }

  /* back */
  .back__band {
    position: absolute; left: 0; width: 100%; background: var(--cream);
  }
  .back__band--top { top: 0; height: 50px; }
  .back__band--bottom { bottom: 0; height: 45px; }
  .back__lace {
    position: absolute; left: 0; width: 100%; height: 42px;
    background: linear-gradient(var(--mustard), #dcc58c);
  }
  .back__lace--top { top: 40px; }
  .back__lace--bottom { bottom: 42px; }
  .person {
    position: absolute; left: 31px; top: 128px; margin: 0;
    font-size: 69px; font-weight: 400; line-height: 94px; color: var(--ink);
  }
  .role {
    position: absolute; left: 31px; top: 360px; margin: 0;
    font-size: 40px; font-style: italic; color: var(--white);
  }
  .contacts {
    position: absolute; left: 33px; top: 462px; margin: 0; padding: 0;
    list-style: none;
  }
  .contacts li {
    display: flex; align-items: center; height: 24px; margin-bottom: 24.5px;
    font-size: 18px; font-style: italic; color: var(--ink);
  }
  .contacts svg { width: 24px; height: 24px; margin-right: 15px; flex: none; }
</style>
</head>
<body>
<main class="canvas">
  <section class="card card--front">
    <div class="front__top"></div>
    <div class="front__lace" role="img" aria-label="Lace trim band"></div>
    <div class="front__dress-form" role="img" aria-label="Illustration of a vintage dress form on a stand"></div>
    <div class="brand">
      <span class="brand__word">Verona</span>
      <span class="brand__by">by</span>
      <span class="brand__word">Kettle</span>
    </div>
  </section>

  <section class="card card--back">
    <div class="back__band back__band--top"></div>
    <div class="back__lace back__lace--top" role="img" aria-label="Mustard lace border"></div>
    <h1 class="person">Miriam<br>Kettle</h1>
    <p class="role">Fashion Designer</p>
    <ul class="contacts">
      <li>
        <svg viewBox="0 0 24 24" aria-hidden="true"><circle cx="12" cy="12" r="12" fill="#3d3c40"/><path d="M6 11c0-3 3-4 6-4s6 1 6 4l-2.5 1-1-2h-5l-1 2z" fill="#f1eee6"/><rect x="8" y="13" width="8" height="4" rx="1" fill="#f1eee6"/></svg>
        04 0261 5847
      </li>
      <li>
        <svg viewBox="0 0 24 24" aria-hidden="true"><circle cx="12" cy="12" r="12" fill="#3d3c40"/><rect x="6" y="8" width="12" height="8" fill="none" stroke="#f1eee6" stroke-width="1.5"/><path d="M6 8l6 5 6-5" fill="none" stroke="#f1eee6" stroke-width="1.5"/></svg>
        veronabykettle@mailbrook.example
      </li>
      <li>
        <svg viewBox="0 0 24 24" aria-hidden="true"><circle cx="12" cy="12" r="12" fill="#3d3c40"/><path d="M8 12h8M13 9l3 3-3 3" fill="none" stroke="#f1eee6" stroke-width="1.8"/></svg>
        www.socialpage.example/VEronaByKettle
      </li>
    </ul>
    <div class="back__lace back__lace--bottom" role="img" aria-label="Mustard lace border"></div>
    <div class="back__band back__band--bottom"></div>
  </section>
</main>
</body>
</html>
```